Dunmore Roofing

Want a professional looking business card

Industry/Entity Type

Business

Contact Information for Business Card

Paul Dunmore ( Owner) paul@dunmoreroofing-example.com, www.dunmoreroofing-example.com, Adress: 4172 Township road 43 Larkfield,ON K9X4T2

```html
<!DOCTYPE html>
<html lang="en">
<head>
<meta charset="utf-8">
<title>Dunmore Roofing – Business Card</title>
<link href="https://fonts.googleapis.com/css2?family=Roboto:wght@400;500;700&family=Roboto+Condensed:wght@500&display=swap" rel="stylesheet">
<style>
  :root {
    --stage: #2a2a2a;
    --card-dark: #1b1b1b;
    --brand-blue: #1a4584;
    --strip-grey: #7b7b7b;
    --ink-light: #ffffff;
  }
  * { margin: 0; padding: 0; box-sizing: border-box; }
  html, body { width: 1200px; height: 960px; overflow: hidden; }
  body {
    background: var(--stage);
    font-family: "Roboto", Arial, sans-serif;
    position: relative;
  }
  .card {
    position: absolute;
    width: 600px;
    height: 343px;
    overflow: hidden;
  }
  .company-name {
    position: absolute;
    font-family: "Roboto", Arial, sans-serif;
    font-weight: 700;
    text-transform: uppercase;
    line-height: 1;
    white-space: nowrap;
  }
  /* Front side */
  .card-front { left: 314px; top: 113px; background: var(--card-dark); }
  .card-front .band { position: absolute; left: 0; top: 0; }
  .card-front .company-name {
    left: 34px; top: 92px;
    font-size: 30px; color: var(--brand-blue);
  }
  .contact-list {
    position: absolute; left: 32px; top: 262px;
    list-style: none; color: var(--ink-light); font-size: 14px;
  }
  .contact-list li { display: flex; align-items: center; height: 19px; }
  .contact-list svg { width: 12px; height: 12px; margin-right: 10px; fill: var(--ink-light); flex: none; }
  .owner {
    position: absolute; right: 30px; top: 221px;
    text-align: right; color: var(--ink-light);
  }
  .owner .name { font-family: "Roboto Condensed", Arial, sans-serif; font-weight: 500; font-size: 23px; text-transform: uppercase; }
  .owner .role { font-size: 15px; font-weight: 500; text-transform: uppercase; margin-top: 2px; }
  .owner .address { font-size: 14px; margin-top: 14px; line-height: 18px; }
  /* Back side */
  .card-back { left: 311px; top: 472px; background: var(--brand-blue); }
  .card-back .company-name {
    left: 0; right: 0; top: 148px;
    text-align: center; font-size: 40px; color: var(--ink-light);
  }
  .card-back .site {
    position: absolute; left: 0; right: 0; top: 285px;
    text-align: center; color: var(--ink-light); font-size: 15px; letter-spacing: 4.2px;
  }
</style>
</head>
<body>
  <section class="card card-front">
    <svg class="band" width="600" height="343" viewBox="0 0 600 343">
      <polygon points="0,222 318,222 305,235 0,235" fill="var(--strip-grey)"/>
      <polygon points="341,200 600,200 600,343 0,343 0,235 306,235" fill="var(--brand-blue)"/>
    </svg>
    <div class="company-name">Dunmore Roofing</div>
    <ul class="contact-list">
      <li><svg viewBox="0 0 24 24"><path d="M6.6 10.8a15 15 0 0 0 6.6 6.6l2.2-2.2c.3-.3.7-.4 1-.2 1.1.4 2.3.6 3.6.6.6 0 1 .4 1 1V20c0 .6-.4 1-1 1A17 17 0 0 1 3 4c0-.6.4-1 1-1h3.5c.6 0 1 .4 1 1 0 1.3.2 2.5.6 3.6.1.3 0 .7-.2 1z"/></svg>613 555 0148</li>
      <li><svg viewBox="0 0 24 24"><path d="M2 5h20v2l-10 7L2 7z"/><path d="M2 9l10 7 10-7v10H2z"/></svg>paul@dunmoreroofing-example.com</li>
      <li><svg viewBox="0 0 24 24"><circle cx="12" cy="12" r="10"/><path d="M2 12h20M12 2c3 3 3 17 0 20M12 2c-3 3-3 17 0 20" stroke="var(--brand-blue)" stroke-width="1.6" fill="none"/></svg>www.dunmoreroofing-example.com</li>
    </ul>
    <div class="owner">
      <div class="name">Paul Dunmore</div>
      <div class="role">Owner</div>
      <div class="address">4172 Township road 43<br>Larkfield, ON K9X4T2</div>
    </div>
  </section>

  <section class="card card-back">
    <div class="company-name">Dunmore Roofing</div>
    <div class="site">www.dunmoreroofing-example.com</div>
  </section>
</body>
</html>
```